Landingpage Design X-Mas Invitation

Every year we invite customers to a special X-Mas Apéro. Since we are an IT-Company we handle the registration process by a landingpage. For this we need a design for the event 2016. The content will be the same as 2015 (you will finde the design attached from last year. There will be an additional job for creating the E-Mail.

Target Market(s)

Customers of IT Company, medium Companys in Central Switzerland

Industry/Entity Type

It Company

Number of Pages Required

1 page

Requirements
Must have
• Christmas Style

```html
<!DOCTYPE html>
<html lang="de">
<head>
<meta charset="utf-8">
<title>Lumora Weihnachtsapéro</title>
<link rel="stylesheet" href="https://fonts.googleapis.com/css2?family=Fira+Sans:wght@300;400;500;600&display=swap">
<style>
  :root {
    --brand-red: #c9402f;
    --text-red: #d2493a;
    --green-light: #d8efc4;
    --green-mid: #a8d98a;
    --band-top: #75b62a;
    --band-bottom: #3d8410;
    --footer-top: #d9624e;
    --footer-bottom: #b2301f;
    --grey-line: #c9c9c9;
    --grey-arrow: #a0a0a0;
    --white: #ffffff;
  }
  * { margin: 0; padding: 0; box-sizing: border-box; }
  html, body { width: 804px; height: 1200px; overflow: hidden; background: var(--white); }
  body { font-family: "Fira Sans", sans-serif; position: relative; }

  .hero { position: absolute; left: 0; top: 0; width: 804px; height: 450px; }
  .hero-sky {
    position: absolute; inset: 0 0 auto 0; height: 240px;
    background: radial-gradient(ellipse at 60% 20%, var(--green-light) 0%, var(--green-mid) 70%, #8fcd6d 100%);
  }
  .hero-clouds { position: absolute; left: 0; top: 0; }
  .branch-ornament {
    position: absolute; left: 0; top: 0; width: 80px; height: 125px;
    background: linear-gradient(160deg, #3c7a2a 0%, #6aa84a 60%, rgba(106,168,74,0) 100%);
    border-bottom-right-radius: 80px 125px;
  }
  .brand { position: absolute; left: 290px; top: 20px; text-align: right; color: var(--brand-red); }
  .brand-name { display: block; font-size: 46px; font-weight: 500; line-height: 46px; letter-spacing: -0.5px; }
  .brand-sub { display: block; font-size: 13px; font-weight: 400; color: var(--brand-red); letter-spacing: 0.5px; margin-top: 2px; }

  .santa-illustration {
    position: absolute; left: 292px; top: 185px; width: 212px; height: 176px;
    border-radius: 40% 40% 30% 30%;
    background: radial-gradient(ellipse at 50% 45%, #f7d9c4 0%, #e04a3c 45%, rgba(224,74,60,0.15) 85%, rgba(255,255,255,0) 100%);
  }
  .tilted {
    position: absolute; color: var(--text-red); font-weight: 300; font-size: 18px;
    line-height: 24px; text-transform: uppercase; white-space: nowrap;
  }
  .event-title { left: 214px; top: 175px; transform: rotate(40deg); transform-origin: left top; text-align: left; }
  .event-title span { display: block; }
  .event-title .l2 { margin-left: -18px; }
  .event-title .l3 { margin-left: -4px; }
  .event-date { left: 480px; top: 260px; transform: rotate(-40deg); text-align: right; }
  .event-date span { display: block; }
  .event-place { left: 172px; top: 360px; transform: rotate(-28deg); text-align: right; }
  .event-place span { display: block; }

  .invitation {
    position: absolute; left: 40px; top: 464px; width: 724px;
    color: var(--text-red); font-size: 14.5px; line-height: 24px; text-align: center;
  }
  .invitation p + p { margin-top: 8px; }

  .register-button {
    position: absolute; left: 321px; top: 715px; width: 159px; height: 38px;
    background: linear-gradient(#d5503f, #b6321f); color: var(--white);
    font-size: 19px; line-height: 38px; text-align: center; text-decoration: none;
    border-radius: 2px; letter-spacing: 0.5px;
  }

  .contact {
    position: absolute; left: 0; top: 788px; width: 804px; height: 214px;
    background: linear-gradient(var(--band-top), var(--band-bottom));
    color: var(--white); text-align: center;
  }
  .contact h2 { font-size: 29px; font-weight: 500; margin-top: 23px; line-height: 38px; letter-spacing: 0.5px; }
  .contact address { font-style: normal; font-size: 17px; line-height: 24px; margin-top: 9px; }

  .partners { position: absolute; left: 0; top: 1040px; width: 804px; height: 56px; }
  .partner-badge {
    position: absolute; top: 3px; width: 138px; height: 50px;
    border: 1px solid var(--grey-line); background: var(--white);
  }
  .partner-badge::after {
    content: ""; position: absolute; left: 34px; top: 18px; width: 70px; height: 14px;
    background: #e6e6e6; border-radius: 2px;
  }
  .carousel-arrow { position: absolute; top: 18px; }

  .footer {
    position: absolute; left: 0; top: 1126px; width: 804px; height: 74px;
    background: linear-gradient(var(--footer-top), var(--footer-bottom));
    color: var(--white); font-size: 13.5px; text-align: center; line-height: 68px;
  }
</style>
</head>
<body>
  <header class="hero">
    <div class="hero-sky"></div>
    <svg class="hero-clouds" width="804" height="450" viewBox="0 0 804 450" aria-hidden="true">
      <g fill="#ffffff">
        <circle cx="120" cy="240" r="160"/>
        <circle cx="430" cy="300" r="200"/>
        <circle cx="640" cy="230" r="88"/>
        <circle cx="790" cy="250" r="150"/>
        <rect x="0" y="240" width="804" height="210"/>
      </g>
    </svg>
    <div class="branch-ornament" role="img" aria-label="Tannenzweig mit goldener Schleife und Lichterkette"></div>
    <div class="brand">
      <span class="brand-name">Lumora</span>
      <span class="brand-sub">IT SOLUTIONS</span>
    </div>

    <div class="santa-illustration" role="img" aria-label="Illustration eines winkenden Weihnachtsmanns"></div>

    <div class="tilted event-title"><span>Lumora</span><span class="l2">Weihnachts</span><span class="l3">Apéro</span></div>
    <div class="tilted event-date"><span>17. Dezember 2015</span><span>17 – 20 Uhr</span></div>
    <div class="tilted event-place"><span>Skylounge</span><span>Tannenweg 12</span><span>Luzern</span></div>
  </header>

  <section class="invitation">
    <p>Unser traditioneller Lumora Weihnachtsapéro findet am Donnerstag, dem 17.12.2015, zwischen 17 und 20 Uhr in unserer Skylounge am Tannenweg 12, dem Hauptsitz der Lumora IT Solutions AG statt. In einem aussergewöhnlichen Ambiente können Sie und Ihre Begleitung köstliche Speisen und Getränke beim Apéro Riche geniessen. Desweiteren bietet sich Ihnen die Gelegenheit, ausgiebige Gespräche mit unserer Geschäftsleitung, unseren Mitarbeitenden sowie weiteren Kunden zu führen. Der Anlass findet in einer lockeren Atmosphäre statt, entsprechend ungezwungen ist der Dresscode.</p>
    <p>Ob Sie den ganzen Abend bleiben oder nur kurz nach dem Weihnachts-Shopping vorbeischauen, ist ganz Ihnen überlassen. Wir freuen uns sehr, wenn Sie uns die Gelegenheit geben, Ihnen mit dieser Einladung für die erfolgreiche Zusammenarbeit herzlichst zu danken.</p>
  </section>

  <a class="register-button" href="#anmelden">ANMELDEN</a>

  <section class="contact">
    <h2>KONTAKT</h2>
    <address>
      Lumora IT Solutions AG<br>
      Tannenweg 12<br>
      6003 Luzern<br>
      Telefon 041 555 01 23<br>
      E-Mail info@lumora-it.ch
    </address>
  </section>

  <section class="partners" aria-label="Partner">
    <svg class="carousel-arrow" style="left:30px" width="14" height="20" viewBox="0 0 14 20" aria-hidden="true"><polyline points="11,2 3,10 11,18" fill="none" stroke="var(--grey-arrow)" stroke-width="2"/></svg>
    <div class="partner-badge" style="left:76px"></div>
    <div class="partner-badge" style="left:246px"></div>
    <div class="partner-badge" style="left:416px"></div>
    <div class="partner-badge" style="left:586px"></div>
    <svg class="carousel-arrow" style="left:757px" width="14" height="20" viewBox="0 0 14 20" aria-hidden="true"><polyline points="3,2 11,10 3,18" fill="none" stroke="var(--grey-arrow)" stroke-width="2"/></svg>
  </section>

  <footer class="footer">© 2016 LUMORA IT SOLUTIONS. All Rights Reserved.</footer>
</body>
</html>
```